Business Card Design

I am a realtor and i also flip houses. I am CEO and Founder of my business which is Voskell Group LLC which is named after my great uncle who died and i was really close to. He was a wonderful friendly man so i want my business to represent him too. My business works with a lot of different people but i want mainly something to show i am a strong confidant woman who owns there own business. I have a really fun personality so i don't want anything TOO serious or manly. I want the perfect mix. My last two business cards i created are too embarrassing to hand out because they are far too girly and i deal with a lot of millionaire clients. I live out in the Palm Springs California area. I think its very important to show i am a single mom, female with her own business at only 24. I don't want to just be a female that blends in with all of the other serious people but yet i don't want to seem immature. People are telling me to stay away from pinks and purples but i don't want blues and greens because they represent men more. But i won't say no to them if there is a happy medium.

Industry/Entity Type

Realtor

Contact Information for Business Card

Voskell Group, LLC
Corinne Tabb
27358 Halvern Ave, C2 517
Sandor Hollow, WA 98431
760-419-6735
Corinnedtabb@mailvane.com

```html
<!DOCTYPE html>
<html lang="en">
<head>
<meta charset="utf-8">
<title>Voskell Group LLC – Business Card</title>
<link rel="stylesheet" href="https://fonts.googleapis.com/css2?family=Aldrich&display=swap">
<style>
  :root {
    --card-teal: #0097a0;
    --bar-pink: #f99fcb;
    --headline-mint: #b9f0c0;
    --contact-aqua: #c2eef0;
    --icon-teal: #0b7a86;
  }
  html, body {
    margin: 0;
    padding: 0;
    width: 1200px;
    height: 702px;
    overflow: hidden;
    background: var(--card-teal);
  }
  .business-card {
    display: block;
    width: 1200px;
    height: 702px;
  }
  .card-background { fill: var(--card-teal); }
  .accent-bar { fill: var(--bar-pink); }
  .card-text { font-family: "Aldrich", sans-serif; }
  .company-name, .person-name { fill: var(--headline-mint); font-size: 48px; }
  .contact-line { fill: var(--contact-aqua); font-size: 33px; }
  .contact-email { font-size: 32px; }
  .contact-icon { fill: var(--icon-teal); }
  .contact-icon-line { stroke: var(--card-teal); stroke-width: 2.5; fill: none; }
</style>
</head>
<body>
<svg class="business-card" viewBox="0 0 1200 702" xmlns="http://www.w3.org/2000/svg" aria-label="Voskell Group LLC business card for Corinne Tabb">
  <rect class="card-background" x="0" y="0" width="1200" height="702"/>

  <g class="accent-bars accent-bars--left">
    <rect class="accent-bar" x="0" y="55" width="442" height="27"/>
    <rect class="accent-bar" x="2" y="119" width="344" height="27"/>
    <rect class="accent-bar" x="0" y="194" width="252" height="27"/>
    <rect class="accent-bar" x="0" y="262" width="185" height="26"/>
    <rect class="accent-bar" x="0" y="328" width="125" height="26"/>
    <rect class="accent-bar" x="0" y="404" width="185" height="27"/>
    <rect class="accent-bar" x="0" y="480" width="259" height="27"/>
    <rect class="accent-bar" x="0" y="547" width="354" height="26"/>
    <rect class="accent-bar" x="2" y="622" width="444" height="26"/>
  </g>

  <g class="accent-bars accent-bars--right">
    <rect class="accent-bar" x="1070" y="64" width="126" height="27"/>
    <rect class="accent-bar" x="933" y="131" width="263" height="27"/>
    <rect class="accent-bar" x="820" y="206" width="376" height="27"/>
    <rect class="accent-bar" x="690" y="267" width="506" height="27"/>
    <rect class="accent-bar" x="599" y="332" width="597" height="27"/>
    <rect class="accent-bar" x="686" y="404" width="510" height="27"/>
    <rect class="accent-bar" x="825" y="475" width="371" height="26"/>
    <rect class="accent-bar" x="932" y="539" width="264" height="26"/>
    <rect class="accent-bar" x="1070" y="608" width="126" height="27"/>
  </g>

  <g class="card-text">
    <text class="company-name" x="376" y="157" textLength="434" lengthAdjust="spacingAndGlyphs">Voskell Group LLC</text>
    <text class="person-name" x="286" y="227" textLength="326" lengthAdjust="spacingAndGlyphs">Corinne Tabb</text>

    <text class="contact-line contact-street" x="215" y="295" textLength="340" lengthAdjust="spacingAndGlyphs">27358 Halvern Ave</text>
    <text class="contact-line contact-city" x="168" y="359" textLength="397" lengthAdjust="spacingAndGlyphs">C2 517 Sandor Hollow</text>
    <text class="contact-line contact-state" x="224" y="429" textLength="170" lengthAdjust="spacingAndGlyphs">WA 98431</text>

    <text class="contact-line contact-phone" x="353" y="509" textLength="265" lengthAdjust="spacingAndGlyphs">760-419-6735</text>
    <text class="contact-line contact-email" x="431" y="574" textLength="469" lengthAdjust="spacingAndGlyphs">corinnedtabb@mailvane.com</text>
  </g>

  <g class="phone-icon" transform="translate(298 477)">
    <path class="contact-icon" d="M8 2 C4 3 1 7 2 13 C5 26 16 37 29 40 C35 41 39 38 40 34 L40 31 L31 24 L26 29 C20 26 16 22 13 16 L18 11 L11 2 Z"/>
  </g>

  <g class="email-icon" transform="translate(371 541)">
    <rect class="contact-icon" x="0" y="0" width="46" height="35"/>
    <path class="contact-icon-line" d="M2 3 L23 20 L44 3 M2 33 L17 16 M44 33 L29 16"/>
  </g>
</svg>
</body>
</html>
```